Velk Partners Building Business Cards

We need a business card that reflects our business as "Solar Experts" in San Diego. Browse our website www.velkpartners.example our License needs to be displayed as "CSLB# 3867140" our phone number is (619) 555-0187

Save thousands on your electric bills and increase the value of your home while helping to protect the environment. Our solar installation experts will help you design the system that's right for you, using only the highest quality equipment that will look great and give you ideal performance. Our goal is to make you energy independent, and get your electric bill to 0.

Paul Osterby
(619) 555-0187
paul@velkpartners.example

Target Market(s)

Home owners in san diego looking for solar

Industry/Entity Type

Solar Energy

Contact Information for Business Card

Paul Osterby
(619) 555-0187
paul@velkpartners.example

Font styles to use
Other font styles liked:
• Use our logo font

Requirements
Must have
• License needs to be displayed as "CSLB# 3867140" our phone number is (619) 555-0187
Nice to have
• Real images of rooftop home solar in san diego
Should not have
• our business address

```html
<!DOCTYPE html>
<html lang="en">
<head>
<meta charset="utf-8">
<title>Velk Partners Building – Business Cards</title>
<link rel="stylesheet" href="https://fonts.googleapis.com/css2?family=Roboto:wght@400;500;700&display=swap">
<style>
  :root {
    --backdrop: #a9a7a7;
    --navy: #24437a;
    --navy-deep: #1f3b6e;
    --navy-light: #2f5090;
    --gold: #eeaa1e;
    --paper: #f7f7f5;
    --white: #ffffff;
  }
  * { margin: 0; padding: 0; box-sizing: border-box; }
  html, body {
    width: 1200px; height: 1200px; overflow: hidden;
    background: var(--backdrop);
    font-family: "Roboto", Arial, sans-serif;
  }
  .canvas { position: relative; width: 1200px; height: 1200px; }

  .card { position: absolute; border-radius: 24px; overflow: hidden; }

  /* Front */
  .card-front {
    left: 238px; top: 117px; width: 713px; height: 420px;
    background: var(--navy);
  }
  .front-photo {
    position: absolute; inset: 0;
    background: linear-gradient(160deg, var(--navy-light) 0%, var(--navy) 45%, var(--navy-deep) 100%);
  }
  .front-brand {
    position: absolute; left: 0; right: 0; top: 148px;
    text-align: center; color: var(--white);
    font-weight: 700; font-size: 54px; letter-spacing: -1px;
  }
  .front-license {
    position: absolute; left: 0; right: 0; top: 364px;
    display: flex; justify-content: center; align-items: center; gap: 20px;
    color: var(--white); font-size: 18px;
  }
  .front-license .rule { width: 55px; height: 3px; background: var(--gold); }

  /* Back */
  .card-back {
    left: 231px; top: 644px; width: 711px; height: 416px;
    background: var(--paper);
  }
  .back-shapes { position: absolute; inset: 0; }
  .person-name {
    position: absolute; left: 44px; top: 48px;
    color: var(--white); font-weight: 700; font-size: 24px;
  }
  .person-title {
    position: absolute; left: 44px; top: 81px;
    color: var(--white); font-size: 16px;
  }
  .contact-list {
    position: absolute; left: 44px; top: 265px; list-style: none;
    color: var(--white); font-size: 18px;
  }
  .contact-list li { display: flex; align-items: center; gap: 16px; height: 25px; }
  .contact-list svg { width: 20px; height: 16px; fill: var(--white); }
  .back-license {
    position: absolute; left: 44px; top: 348px;
    color: var(--white); font-size: 18px;
  }
  .back-brand {
    position: absolute; left: 420px; width: 290px; top: 150px;
    display: flex; flex-direction: column; align-items: center; gap: 16px;
  }
  .back-brand .mark { width: 56px; height: 56px; border-radius: 50%; background: var(--gold); }
  .back-brand .name {
    color: var(--navy); font-weight: 700; font-size: 24px; text-align: center; line-height: 1.25;
  }
</style>
</head>
<body>
<main class="canvas">

  <section class="card card-front">
    <div class="front-photo" role="img" aria-label="Rooftop solar panel array photo in blue tones"></div>
    <div class="front-brand">Velk Partners Building</div>
    <div class="front-license">
      <span class="rule"></span>
      <span>License: CSLB# 3867140</span>
      <span class="rule"></span>
    </div>
  </section>

  <section class="card card-back">
    <svg class="back-shapes" viewBox="0 0 711 416" preserveAspectRatio="none" aria-hidden="true">
      <path d="M0,0 H434 C362,120 345,300 434,416 H0 Z" fill="var(--navy)"/>
      <path d="M440,0 H466 C398,92 370,230 378,362 C364,240 382,100 440,0 Z" fill="var(--gold)"/>
    </svg>

    <div class="person-name">Paul Osterby</div>
    <div class="person-title">Managing Director</div>

    <ul class="contact-list">
      <li>
        <svg viewBox="0 0 20 16"><path d="M2 4c0-2 3-3 8-3s8 1 8 3v2h-4V4.5c-1-.5-2.5-.7-4-.7s-3 .2-4 .7V6H2z M4 8h12l2 7H2z"/></svg>
        <span>(619) 555-0187</span>
      </li>
      <li>
        <svg viewBox="0 0 20 16"><path d="M10 1a7 7 0 1 0 0 14A7 7 0 0 0 10 1zm0 1.5c.9 0 2 1.9 2.3 4.7H7.7C8 4.4 9.1 2.5 10 2.5zM7.7 8.8h4.6c-.3 2.8-1.4 4.7-2.3 4.7s-2-1.9-2.3-4.7zM4.5 7.2a5.6 5.6 0 0 1 2.4-4c-.4.9-.7 2.3-.8 4zm0 1.6h1.6c.1 1.7.4 3.1.8 4a5.6 5.6 0 0 1-2.4-4zm11 0a5.6 5.6 0 0 1-2.4 4c.4-.9.7-2.3.8-4zm0-1.6h-1.6c-.1-1.7-.4-3.1-.8-4a5.6 5.6 0 0 1 2.4 4z"/></svg>
        <span>paul@velkpartners.example</span>
      </li>
      <li>
        <svg viewBox="0 0 20 16"><path d="M1 2h18v12H1zm2 1.5L10 9l7-5.5zM2.5 4.5v8l5-4zm15 0-5 4 5 4z"/></svg>
        <span>www.velkpartners.example</span>
      </li>
    </ul>
    <div class="back-license">License: CSLB# 3867140</div>

    <div class="back-brand">
      <span class="mark"></span>
      <span class="name">Velk Partners<br>Building</span>
    </div>
  </section>

</main>
</body>
</html>
```